Mosquito and outdoor pest management

The uploaded logo must be integrated as the main theme of the card. I would like it to be modern and eye catching. Maybe some backround images or light silver metallic background.
Space enough at the base for contact info to be put in- phone numbers,emails,names,website.
Space on the back for short blog and lines for hand writing..calling card.
Commercial- golf courses, schools, outdoor function properties, pre event treatments.
Residential- retirement villages, townhome complexes and general houses
Management

```html
<!DOCTYPE html>
<html lang="en">
<head>
<meta charset="utf-8">
<title>Bayline Pest Co. – Business Card</title>
<link href="https://fonts.googleapis.com/css2?family=Cinzel:wght@700&family=Crimson+Text:wght@400&family=Open+Sans:wght@400;600&family=Roboto:wght@400&display=swap" rel="stylesheet">
<style>
  :root{
    --bg:#e9e7e3;
    --paper:#f7f7f6;
    --ink:#1d1d1d;
    --charcoal:#2b2b2c;
    --red:#e0262f;
    --white:#ffffff;
    --shadow:rgba(0,0,0,.18);
  }
  *{margin:0;padding:0;box-sizing:border-box}
  html,body{width:1200px;height:864px;overflow:hidden;background:var(--bg)}
  .canvas{position:relative;width:1200px;height:864px}
  .card{position:absolute;top:278px;width:540px;height:309px;background:var(--paper);
        overflow:hidden;box-shadow:0 6px 18px var(--shadow)}
  .card--front{left:40px}
  .card--back{left:620px}
  .card svg.art{position:absolute;inset:0}

  /* front */
  .brand{position:absolute;left:150px;top:42px;display:flex;align-items:center;gap:10px;
         font-family:"Open Sans",sans-serif;font-weight:600;font-size:28px;color:var(--ink);line-height:1}
  .brand__mark{width:14px;height:14px;background:var(--ink)}
  .contact{position:absolute;right:36px;top:180px;text-align:right;color:var(--white);font-family:"Roboto",sans-serif}
  .contact__name{font-family:"Cinzel",serif;font-weight:700;color:var(--red);font-size:21px;letter-spacing:.5px;line-height:26px}
  .contact__role{font-size:12px;margin:2px 0 10px}
  .contact__line{display:flex;justify-content:flex-end;align-items:center;gap:10px;font-size:13px;letter-spacing:1px;height:19px}
  .contact__icon{width:13px;height:13px;background:var(--red);display:flex;align-items:center;justify-content:center}

  /* back */
  .services{position:absolute;left:40px;top:34px;font-family:"Open Sans",sans-serif;color:var(--ink)}
  .services__head{font-family:"Crimson Text",serif;font-size:17px;margin-bottom:8px}
  .services__list{list-style:none;margin:0 0 10px 26px;font-size:12.5px;line-height:15px}
  .services__list li{position:relative;padding-left:16px}
  .services__list li::before{content:"";position:absolute;left:0;top:5px;width:6px;height:6px;background:var(--red)}
  .emblem{position:absolute;right:40px;top:58px;width:120px;height:90px;border-radius:8px;
          background:radial-gradient(circle,#f3c9cb 0%,#f7f7f6 75%)}
</style>
</head>
<body>
<main class="canvas">

  <section class="card card--front">
    <svg class="art" width="540" height="309" viewBox="0 0 540 309">
      <path d="M0,0 L48,0 C48,130 130,188 270,186 C390,184 450,166 540,190 L540,309 L0,309 Z" fill="var(--charcoal)"/>
      <path d="M48,0 C48,130 130,188 270,186 C390,184 450,166 540,190" fill="none" stroke="var(--red)" stroke-width="5"/>
    </svg>
    <div class="brand">
      <span class="brand__mark"></span>
      <span class="brand__name">Bayline Pest Co.</span>
    </div>
    <div class="contact">
      <div class="contact__name">Dan Harlow</div>
      <div class="contact__role">Director</div>
      <div class="contact__line">(07) 5550 1284
        <span class="contact__icon"><svg width="9" height="9" viewBox="0 0 10 10"><path d="M2 1h2l1 2-1 1c.5 1 1.5 2 2 2l1-1 2 1v2c-4 1-8-3-7-7z" fill="#fff"/></svg></span></div>
      <div class="contact__line">dan@bayline.com
        <span class="contact__icon"><svg width="9" height="9" viewBox="0 0 10 10"><rect x="1" y="2.5" width="8" height="5.5" fill="none" stroke="#fff"/><path d="M1 2.5l4 3 4-3" fill="none" stroke="#fff"/></svg></span></div>
      <div class="contact__line">www.baylinepest.com
        <span class="contact__icon"><svg width="9" height="9" viewBox="0 0 10 10"><circle cx="5" cy="5" r="3.8" fill="none" stroke="#fff"/><path d="M1.2 5h7.6M5 1.2v7.6" stroke="#fff" stroke-width=".8"/></svg></span></div>
    </div>
  </section>

  <section class="card card--back">
    <svg class="art" width="540" height="309" viewBox="0 0 540 309">
      <path d="M40,14 L540,14 L540,16 L40,15 Z" fill="var(--red)"/>
      <path d="M200,22 L500,22 L500,27 L200,23 Z" fill="var(--red)"/>
      <rect x="0" y="224" width="540" height="4" fill="var(--red)"/>
      <path d="M0,228 L165,228 L176,240 L176,262 L0,262 Z" fill="var(--charcoal)"/>
      <rect x="0" y="262" width="540" height="26" fill="var(--red)"/>
    </svg>
    <div class="emblem" role="img" aria-label="Red insect emblem of the brand"></div>
    <div class="services">
      <div class="services__head">Commercial</div>
      <ul class="services__list">
        <li>golf courses,</li>
        <li>schools,</li>
        <li>outdoor function properties,</li>
        <li>pre event treatments.</li>
      </ul>
      <div class="services__head">Residential</div>
      <ul class="services__list">
        <li>retirement villages,</li>
        <li>townhome complexes and general houses.</li>
      </ul>
    </div>
  </section>

</main>
</body>
</html>
```